Flyer for Dessert Cafe event launch

Hi
We are launching a new initiative at our cafe - this is the plan:
- We will open Saturday nights to serve desserts, tea and coffee and other after dinner deliciousness (no alcohol)
- Customers stop in and enjoy something sweets on the way home from dinner or movies. We'd decorate the garden with fairy lights, candles and lanterns and create a beautiful and relaxing (and romantic) after dinner atmosphere - maybe a little acoustic guitar
- For the menu we are thinking everything from chocolate mousse and cheesecake to tiramisu and dessert mocktails and even sorbet and gelato.
- The dessert cafe would probably trade from 7pm till 11pm.
Please check out www.brelvantable.com for our current branding feel.

We need an A4 flyer designed to promote this new venture.
I want the design to incorporate trees with fairy lights in them - and hearts - as we will be launching on Valentines Day evening (and the heart is part of our branding). Obviously the design needs to be tied in with our current branding - logo attached in various forms I am happy for you to use whichever fits best with your design. I have also attached some images that inspire me for this project - but they don't need to be used.

The following information will need to be included:

On the way home from dinner, or just craving something sweet?
Join us for Dessert!
Unwind - Relax - Indulge
7pm - 11pm every Saturday night
Starting on Valentines Day
All desserts handmade in-house - with love! *** Coffee *** Tea *** Mocktails *** Share platters available ***Gluten Free, Dairy Free and Vegan options *** Take-Away Available
Live Music

2847 Ridgeway Drive, Harlow Flats (five minutes from Torquay)
(03) 5391 8264
www.brelvantable.com
Please include the Facebook - Twiiter and Instagram Icons

```html
<!DOCTYPE html>
<html lang="en">
<head>
<meta charset="utf-8">
<title>Brelvan Table Café – Saturday Night Desserts</title>
<link href="https://fonts.googleapis.com/css2?family=Arimo:wght@400&family=Calligraffitti&display=swap" rel="stylesheet">
<style>
  :root {
    --night-navy: #141a4a;
    --night-violet: #3b2a6e;
    --bokeh-blue: #3f6fc4;
    --warm-glow: #d9c48a;
    --candle-cream: #efe2b4;
    --ribbon-red: #c8161d;
    --panel-red: #d41f24;
    --script-red: #e3101c;
    --heart-pink: #ff9fa6;
    --white: #ffffff;
    --sans: "Arimo", Arial, sans-serif;
    --script: "Calligraffitti", "Comic Sans MS", cursive;
  }
  * { box-sizing: border-box; margin: 0; padding: 0; }
  html, body { width: 848px; height: 1200px; overflow: hidden; background: var(--night-navy); }
  .flyer { position: relative; width: 848px; height: 1200px; overflow: hidden; font-family: var(--sans); color: var(--white); }

  .backdrop-photo {
    position: absolute; inset: 0;
    background:
      radial-gradient(ellipse 260px 220px at 150px 860px, rgba(150,40,40,.55), transparent 70%),
      radial-gradient(ellipse 420px 260px at 260px 760px, var(--candle-cream), transparent 75%),
      radial-gradient(ellipse 300px 200px at 700px 280px, rgba(240,120,90,.5), transparent 70%),
      radial-gradient(ellipse 380px 300px at 560px 520px, rgba(90,140,230,.7), transparent 70%),
      radial-gradient(ellipse 320px 220px at 120px 360px, rgba(220,110,60,.45), transparent 70%),
      linear-gradient(180deg, var(--night-violet) 0%, var(--night-navy) 30%, var(--bokeh-blue) 48%, var(--warm-glow) 66%, #9a8a6a 82%, #223a7a 100%);
  }

  .brand-mark { position: absolute; left: -10px; top: -12px; width: 250px; height: 250px; }
  .brand-ring { position: absolute; inset: 0; border: 1.5px solid rgba(255,255,255,.85); border-radius: 50%; }
  .brand-name {
    position: absolute; left: 22px; top: 100px; width: 220px;
    font-size: 30px; line-height: 34px; font-weight: 400; color: var(--white); white-space: nowrap;
  }
  .brand-lace { position: absolute; left: 175px; top: 0; width: 120px; height: 150px; background: rgba(255,255,255,.14); border-radius: 0 0 60px 60px; }

  .headline {
    position: absolute; left: 370px; top: 34px; width: 400px;
    font-size: 40px; line-height: 51px; font-weight: 400; text-align: center;
    text-shadow: 0 0 3px #000, 0 0 8px rgba(0,0,0,.6);
  }

  .ribbon { position: absolute; left: 0; top: 220px; width: 848px; height: 150px; }
  .ribbon-text {
    position: absolute; left: 0; width: 848px; top: 280px;
    text-align: center; font-family: var(--script); font-size: 50px; line-height: 64px; color: var(--white);
  }

  .launch-date {
    position: absolute; left: 50px; top: 478px; width: 400px; text-align: center;
    font-family: var(--script); font-size: 50px; line-height: 76px; color: var(--script-red);
    text-shadow: 0 0 4px #fff, 0 0 8px #fff, 0 0 14px rgba(255,255,255,.8);
  }

  .lace-ornament { position: absolute; left: 470px; width: 340px; height: 100px; background: rgba(255,255,255,.16); border-radius: 50%; }
  .lace-top { top: 360px; }
  .lace-bottom { top: 955px; }

  .menu-panel {
    position: absolute; left: 510px; top: 460px; width: 262px; height: 490px;
    background: var(--panel-red); text-align: center;
    box-shadow: 0 0 0 1px rgba(255,255,255,.5);
  }
  .menu-intro { font-family: var(--script); padding-top: 30px; }
  .menu-intro .big { display: block; font-size: 34px; line-height: 56px; }
  .menu-intro .small { display: block; font-size: 18px; line-height: 24px; margin-top: 4px; }
  .menu-list { list-style: none; margin-top: 30px; }
  .menu-list li {
    font-size: 18px; line-height: 26px; padding: 7px 0 8px; margin: 0 8px;
    border-bottom: 1px solid rgba(255,255,255,.45); white-space: nowrap;
  }
  .menu-list li:last-child { border-bottom: none; }
  .heart { color: var(--heart-pink); font-size: 12px; padding: 0 2px; }

  .hours { position: absolute; left: 26px; top: 1055px; font-size: 31px; text-shadow: 0 0 4px rgba(0,0,0,.5); }
  .contact { position: absolute; left: 80px; top: 1102px; font-size: 18px; line-height: 29px; font-style: normal; }
  .contact .web { font-size: 22px; }

  .social-links { position: absolute; left: 524px; top: 1110px; display: flex; gap: 14px; }
  .social-tile { width: 70px; height: 70px; background: var(--white); border-radius: 6px; }
</style>
</head>
<body>
<main class="flyer">
  <div class="backdrop-photo" role="img" aria-label="Night garden with blurred fairy lights in blue, violet and gold, and a red gingham fabric heart hanging on a string"></div>

  <header class="brand-mark">
    <div class="brand-ring"></div>
    <div class="brand-lace" role="img" aria-label="Lace ornament"></div>
    <div class="brand-name">brelvan table<br>café</div>
  </header>

  <h1 class="headline">On the way<br>home from dinner,<br>or just craving<br>something sweet?</h1>

  <svg class="ribbon" viewBox="0 0 848 150" aria-hidden="true">
    <path d="M0 22 Q420 60 848 0 L848 95 Q420 140 0 120 Z" fill="var(--ribbon-red)" opacity=".93"/>
    <path d="M0 22 Q420 60 848 0" fill="none" stroke="#fff" stroke-width="3"/>
  </svg>
  <p class="ribbon-text">Join us for Dessert !</p>

  <p class="launch-date">Starting on<br>Valentines Day</p>

  <div class="lace-ornament lace-top" role="img" aria-label="White lace scroll ornament"></div>
  <section class="menu-panel">
    <p class="menu-intro"><span class="big">All desserts<br>handmade</span><span class="small">in-house with love!</span></p>
    <ul class="menu-list">
      <li>Coffee<span class="heart">♥</span>Tea<span class="heart">♥</span>Mocktails</li>
      <li>Share platters available</li>
      <li>Gluten Free<span class="heart">♥</span>Dairy Free<br>and Vegan options</li>
      <li>Take-Away Available</li>
      <li>Unwind<span class="heart">♥</span>Relax<span class="heart">♥</span>Indulge</li>
      <li>Live Music</li>
    </ul>
  </section>
  <div class="lace-ornament lace-bottom" role="img" aria-label="White lace scroll ornament"></div>

  <p class="hours">7pm - 11pm every Saturday night</p>
  <address class="contact">
    2847 Ridgeway Drive, Harlow Flats<br>
    (five minutes from Torquay)<br>
    (03) 5391 8264 • <span class="web">www.brelvantable.com</span>
  </address>

  <nav class="social-links" aria-label="Social media">
    <div class="social-tile" role="img" aria-label="Social network link"></div>
    <div class="social-tile" role="img" aria-label="Social network link"></div>
    <div class="social-tile" role="img" aria-label="Social network link"></div>
  </nav>
</main>
</body>
</html>
```